Set up small scale company website

We need a website set up for our educational consultancy - Vexmore Education. We like the following site and want something similar www.plindarhub.co.uk We can provide the copy and images but need the following:- setting up the overall theme and design - to our requirements on colours and forma- Approximately 4 pages of services offered and with an index pageEtct (yellow and green)And the following pages - as well as a home page:- A contact page linked to our email addresses and registered business address 17 Wexbury Lane, Dunmere, Ostshire, CO14 8PN- About Us page - An index of services page that links to between 4-6 pages outlining services- A News page that links to updates of latest services, events and activities - easily updated by usOn the homepage we'd like links to chirpnet and WorkLoop feeds and links to our other blogs and websites
Target Market(s)
Schools, local authoroties and multi-academy trusts
Logo Text
Vexmore Education
Coding
Coded - Design and coding required
Number of Pages Required
5+ page
Font styles to use
Requirements
Should not have
- No tacky pictures of mortar boards or chalk boards etc.

```html
<!DOCTYPE html>
<html lang="en">
<head>
<meta charset="utf-8">
<title>Vexmore Education</title>
<link href="https://fonts.googleapis.com/css2?family=Montserrat:wght@400;500;600;700&family=Open+Sans:wght@400;600&display=swap" rel="stylesheet">
<style>
:root{
  --green:#7dbb2a;
  --green-dark:#6aa51f;
  --yellow:#e3df26;
  --ink:#333a44;
  --muted:#555c66;
  --tint:#eef1f9;
  --navy:#0f1a2d;
  --link:#1f5fae;
  --line:#c9ccd6;
}
*{box-sizing:border-box;margin:0;padding:0}
html,body{width:1200px;height:3025px;overflow:hidden}
body{position:relative;background:#fff;font-family:"Open Sans",Arial,sans-serif;color:var(--ink)}
.abs{position:absolute}
.btn{position:absolute;display:flex;align-items:center;justify-content:center;background:var(--green);color:#fff;font-family:"Montserrat",Arial,sans-serif;font-size:12px;font-weight:500;height:44px;width:96px;border-radius:2px}
h2.section-title{position:absolute;left:0;width:1200px;text-align:center;font-family:"Montserrat",Arial,sans-serif;font-weight:600;color:var(--green);font-size:32px}

/* header */
.site-header{position:absolute;top:0;left:0;width:1200px;height:95px;background:#fff}
.brand{position:absolute;left:145px;top:24px;font-family:"Montserrat",Arial,sans-serif;font-size:34px;font-weight:600;color:var(--green)}
.main-nav{position:absolute;right:145px;top:38px;display:flex;gap:40px;font-family:"Montserrat",Arial,sans-serif;font-size:14px;color:#444}
.main-nav .active{color:var(--green)}

/* hero */
.hero{position:absolute;top:95px;left:0;width:1200px;height:600px;background:linear-gradient(100deg,#9aa7b5 0%,#c7b9a3 35%,#aab2bf 60%,#5a6170 100%)}
.hero-curve{position:absolute;left:0;top:590px}
.hero-caption{position:absolute;left:295px;top:51px;width:610px;height:80px;background:rgba(40,40,40,.72);color:#fff;font-family:"Montserrat",Arial,sans-serif;font-weight:600;font-size:22px;text-align:center;padding-top:14px}
.hero .btn{left:540px;top:109px;width:120px;height:40px;font-weight:600}
.hero-arrow{position:absolute;top:240px;width:38px;height:38px;border-radius:50%;background:var(--yellow)}

/* welcome */
.welcome h2{position:absolute;left:145px;top:765px;font-family:"Montserrat",Arial,sans-serif;font-weight:600;font-size:32px;color:var(--green)}
.welcome p{position:absolute;left:145px;top:818px;width:600px;font-size:13px;line-height:25.5px;color:var(--muted)}
.welcome-photo{position:absolute;left:808px;top:758px;width:242px;height:242px;border-radius:50%;border:3px solid #d8dbe3;background:radial-gradient(circle at 50% 40%,#d8dde6,#8f9bad)}

/* services */
.services-bg{position:absolute;left:0;top:1088px;width:1200px;height:567px}
.service{position:absolute;top:1245px;width:240px;text-align:center}
.service .ring{width:168px;height:168px;margin:0 auto;border-radius:50%;border:3px solid var(--line);display:flex;align-items:center;justify-content:center}
.service h3{margin-top:20px;font-family:"Montserrat",Arial,sans-serif;font-weight:500;font-size:20px;color:var(--green)}
.service p{margin:10px auto 0;width:200px;font-size:10.5px;line-height:17px;color:var(--ink)}
.service .btn{position:relative;margin:16px auto 0}

/* blog */
.post{position:absolute;top:1797px;width:288px}
.post .photo{height:193px}
.post time{display:block;margin-top:18px;font-size:14px;color:#222}
.post h3{margin-top:12px;font-family:"Open Sans",Arial,sans-serif;font-weight:400;font-size:15.5px;line-height:22px;color:var(--green)}
.post p{margin-top:10px;font-size:10.5px;line-height:17px;color:var(--ink)}
.blog-arrow{position:absolute;top:1883px}

/* what's new */
.news-bg{position:absolute;left:0;top:2280px;width:1200px;height:460px}
.card{position:absolute;top:2428px;width:295px;height:228px;background:#fff}
.card .badge{position:absolute;left:0;top:0;width:38px;height:38px}
.card h3{position:absolute;left:50px;top:22px;width:230px;font-weight:400;font-size:16px;line-height:21px;color:var(--link)}
.card p{position:absolute;left:50px;width:230px;font-size:10.5px;line-height:18px;color:#555}
.card .links{position:absolute;left:30px;top:54px;display:grid;grid-template-columns:140px 110px;row-gap:7px;font-size:11.5px;color:#333}
.card .links span{text-decoration:underline}

/* footer */
.site-footer{position:absolute;left:0;top:2737px;width:1200px;height:288px;background:var(--navy);color:#c8cdd6}
.site-footer h4{position:absolute;top:42px;font-family:"Montserrat",Arial,sans-serif;font-weight:600;font-size:15px;color:var(--yellow)}
.foot-links{position:absolute;top:78px;font-size:10.5px;line-height:24px;color:#c8cdd6}
.contact-list{position:absolute;left:385px;top:80px;font-size:10.5px;line-height:16px}
.contact-list li{list-style:none;display:flex;gap:12px;margin-bottom:10px}
.newsletter{position:absolute;left:678px;top:84px;width:220px;height:40px;background:#e9ecf1;border-radius:3px;font-size:11px;color:#333;padding:12px 14px}
.social{position:absolute;left:910px;top:86px;display:flex;gap:14px;font-size:11px}
.social span{display:flex;align-items:center;gap:5px}
.social i{display:inline-block;width:8px;height:8px;border-radius:50%;background:#c8cdd6}
.footer-rule{position:absolute;left:145px;top:214px;width:910px;height:1px;background:#3a4558}
.copyright{position:absolute;left:0;top:242px;width:1200px;text-align:center;font-size:11px}
</style>
</head>
<body>

<header class="site-header">
  <div class="brand">Vexmore Education</div>
  <nav class="main-nav">
    <span class="active">HOME</span><span>SERVICES</span><span>NEWS</span><span>ABOUT US</span><span>CONTACT US</span>
  </nav>
</header>

<section class="hero" role="img" aria-label="Photo of two women in conversation at a desk in front of office shelves">
  <div class="hero-caption">Aliquam consectetur molestie dictum molestie</div>
  <div class="btn">READ MORE</div>
  <div class="hero-arrow" style="left:51px"><svg width="38" height="38"><path d="M22 12 L15 19 L22 26" fill="none" stroke="#222" stroke-width="3"/></svg></div>
  <div class="hero-arrow" style="left:1110px"><svg width="38" height="38"><path d="M16 12 L23 19 L16 26" fill="none" stroke="#222" stroke-width="3"/></svg></div>
</section>
<svg class="hero-curve" width="1200" height="110"><path d="M0 20 Q600 130 1200 22 L1200 110 L0 110 Z" fill="#fff"/></svg>

<section class="welcome">
  <h2>Welcome to Vexmore Education</h2>
  <p>Maecenas vel tortor accumsan quam varius imperdiet vel eget elit. Aenean facilisis tincidunt lectus, id dictum nisi luctus eget. Vivamus efficitur ex condimentum, malesuada eros eget, feugiat nibh. Sed tellus ex, imperdiet eget gravida sit amet, volutpat eget turpis. In nec ultricies est. Etiam mattis augue vehicula odio posuere, sit amet tempus lectus luctus. Nulla facilisi. Etiam vel massa elementum, bibendum tellus venenatis, feugiat massa. Curabitur venenatis lacinia ornare.</p>
  <div class="btn" style="left:145px;top:965px">Read More</div>
  <div class="welcome-photo" role="img" aria-label="Round photo of a teacher helping a student at a laptop"></div>
</section>

<svg class="services-bg" width="1200" height="567"><path d="M0 78 Q600 -40 1200 78 L1200 567 L0 567 Z" fill="#eef1f9"/></svg>
<h2 class="section-title" style="top:1176px">Our Services</h2>

<div class="service" style="left:128px">
  <div class="ring"><svg width="80" height="80" fill="none" stroke="#7dbb2a" stroke-width="2.5"><path d="M40 18 Q25 10 8 14 V66 Q25 62 40 70 Q55 62 72 66 V14 Q55 10 40 18 Z M40 18 V70"/><path d="M16 26 H32 M16 34 H32 M16 42 H32 M16 50 H32 M48 26 H64 M48 34 H64 M48 42 H64 M48 50 H64"/></svg></div>
  <h3>Aliquam erat</h3>
  <p>Aenean placerat, nibh vel accumsan aliquet, magna nibh accumsan nibh, ac tempus nunc ipsum ac tellus</p>
  <div class="btn">Read More</div>
</div>
<div class="service" style="left:362px">
  <div class="ring"><svg width="80" height="80" fill="none" stroke="#7dbb2a" stroke-width="2.5"><path d="M10 70 H70 M16 70 V36 H64 V70 M26 36 V24 H54 V36 M40 10 V24 M40 10 H50 V16 H40"/><path d="M34 70 V56 H46 V70 M22 44 H30 M50 44 H58 M22 54 H28 M52 54 H58 M36 30 H44"/></svg></div>
  <h3>Quisque aliquet</h3>
  <p>Aenean placerat, nibh vel accumsan aliquet, magna nibh accumsan nibh, ac tempus nunc ipsum ac tellus</p>
  <div class="btn">Read More</div>
</div>
<div class="service" style="left:596px">
  <div class="ring"><svg width="80" height="80" fill="none" stroke="#7dbb2a" stroke-width="2.5"><circle cx="40" cy="28" r="14"/><path d="M14 70 Q14 48 40 48 Q66 48 66 70 Z"/></svg></div>
  <h3>Etiam mattis</h3>
  <p>Aenean placerat, nibh vel accumsan aliquet, magna nibh accumsan nibh, ac tempus nunc ipsum ac tellus</p>
  <div class="btn">Read More</div>
</div>
<div class="service" style="left:830px">
  <div class="ring"><svg width="80" height="80" fill="none" stroke="#7dbb2a" stroke-width="2.5"><path d="M6 34 L20 22 L32 30 L44 24 L60 22 L74 34"/><path d="M16 38 L34 56 Q38 60 42 56 L62 38"/><path d="M28 48 L36 42 M34 54 L42 46 M44 30 L30 40"/></svg></div>
  <h3>Nulla facilisi</h3>
  <p>Aenean placerat, nibh vel accumsan aliquet, magna nibh accumsan nibh, ac tempus nunc ipsum ac tellus</p>
  <div class="btn">Read More</div>
</div>

<h2 class="section-title" style="top:1722px">Blog</h2>
<svg class="blog-arrow" style="left:44px" width="20" height="26"><path d="M14 4 L6 13 L14 22" fill="none" stroke="#555" stroke-width="2.5"/></svg>
<svg class="blog-arrow" style="left:1136px" width="20" height="26"><path d="M6 4 L14 13 L6 22" fill="none" stroke="#555" stroke-width="2.5"/></svg>

<article class="post" style="left:145px">
  <div class="photo" role="img" aria-label="Photo of a team meeting around an office table" style="background:linear-gradient(120deg,#e4e8ee,#8da0b8)"></div>
  <time>4 February, 2019</time>
  <h3>Quisque aliquet ex nec est vestibulum pulvinar. Pellentesque convallis.</h3>
  <p>Nunc sit amet consequat risus. Curabitur ac elit leo. In eleifend dui tellus, in scelerisque elit porttitor et. Integer eu massa lacinia, lacinia nulla non, volutpat purus.</p>
</article>
<article class="post" style="left:456px">
  <div class="photo" role="img" aria-label="Photo of two students talking in a library" style="background:linear-gradient(120deg,#4c5360,#b9b3aa)"></div>
  <time>4 February, 2019</time>
  <h3>Etiam id imperdiet lectus. Vivamus lacus justo, ultrices nec.</h3>
  <p>Nunc sit amet consequat risus. Curabitur ac elit leo. In eleifend dui tellus, in scelerisque elit porttitor et. Integer eu massa lacinia, lacinia nulla non, volutpat purus.</p>
</article>
<article class="post" style="left:768px">
  <div class="photo" role="img" aria-label="Photo of students studying at a table among bookshelves" style="background:linear-gradient(120deg,#7a4d38,#c98f5e 50%,#3c3a3e)"></div>
  <time>4 February, 2019</time>
  <h3>Fusce vitae lectus sit amet mi pulvinar maximus. Aenean placerat.</h3>
  <p>Nunc sit amet consequat risus. Curabitur ac elit leo. In eleifend dui tellus, in scelerisque elit porttitor et. Integer eu massa lacinia, lacinia nulla non, volutpat purus.</p>
</article>
<div class="btn" style="left:552px;top:2160px">View All</div>

<svg class="news-bg" width="1200" height="460"><path d="M0 76 Q600 -40 1200 76 L1200 460 L0 460 Z" fill="#eef1f9"/></svg>
<h2 class="section-title" style="top:2363px">What's New</h2>

<div class="card" style="left:145px">
  <div class="badge" style="background:#1d5fa6"></div>
  <h3>Maecenas vel tortor accumsan quam varius imperdiet.</h3>
  <p style="top:82px">&nbsp;Pellentesque convallis molestie enim sit amet efficitur. Etiam id imperdiet lectus. Vivamus lacus justo, ultrices nec. <span style="color:var(--link)">Fusce vitae lectus sit amet mi pulvinar maximus. Aenean placerat, nibh vel accumsan aliquet.</span></p>
</div>
<div class="card" style="left:452px">
  <div class="badge" style="background:var(--green)"><svg width="38" height="38" fill="none" stroke="#fff" stroke-width="2"><rect x="11" y="15" width="10" height="6" rx="3" transform="rotate(-45 16 18)"/><rect x="17" y="17" width="10" height="6" rx="3" transform="rotate(-45 22 20)"/></svg></div>
  <div class="links">
    <span>Maecenas vel</span><span>Fusce vitae</span>
    <span>Etiam mattis augue</span><span>Aenean placerat</span>
    <span>Curabitur venenatis</span><span>Cras augue</span>
    <span>Quisque aliquet</span><span>Phasellus nisl</span>
    <span>Aliquam erat</span><span>Donec sit</span>
    <span>Vivamus lacus</span><span>Aenean feugiat</span>
  </div>
</div>
<div class="card" style="left:760px">
  <div class="badge" style="background:#2aa6e0"></div>
  <h3>Cras eget leo sed nunc hendrerit ultricies eu at nisl.</h3>
  <p style="top:76px">Nulla facilisi. Etiam vel massa elementum, bibendum tellus venenatis, feugiat massa. Curabitur venenatis lacinia ornare. Cras sollicitudin cursus dui eu placerat.</p>
  <p style="top:176px;font-size:10px;font-weight:600;color:#222">January 04, 2019</p>
</div>

<footer class="site-footer">
  <h4 style="left:145px">Links</h4>
  <div class="foot-links" style="left:145px">Home<br>Services<br>News<br>About us</div>
  <div class="foot-links" style="left:216px">Contact us<br>Terms and Condition<br>Privacy Policy</div>

  <h4 style="left:385px">Contact info</h4>
  <ul class="contact-list">
    <li><svg width="10" height="14"><path d="M5 1 A4 4 0 0 1 9 5 C9 8 5 13 5 13 C5 13 1 8 1 5 A4 4 0 0 1 5 1 Z" fill="#c8cdd6"/></svg><span>Mr. Alden Crosby<br>17 Wexbury Lane, Dunmere, Ostshire, CO14 8PN</span></li>
    <li><svg width="10" height="14"><path d="M2 2 L5 2 L6 5 L4 6 Q5 9 8 10 L9 8 L12 9 L12 12 Q5 12 2 2 Z" fill="#c8cdd6" transform="scale(.8)"/></svg><span>Phone : 546 318 2207</span></li>
    <li><svg width="10" height="14"><rect x="0" y="3" width="10" height="8" fill="#c8cdd6"/></svg><span>Email : info@vexmoremail.com</span></li>
  </ul>

  <h4 style="left:678px">Newsletter</h4>
  <div class="newsletter">Email Address
    <svg class="abs" style="right:10px;top:11px" width="20" height="18"><path d="M1 1 L19 1 L19 17 L1 17 Z M1 1 L10 10 L19 1" fill="#222" stroke="#e9ecf1" stroke-width="1"/></svg>
  </div>

  <h4 style="left:955px">Follow us on</h4>
  <div class="social"><span><i></i>Pagecircle</span><span><i></i>chirpnet</span><span><i></i>WorkLoop</span></div>

  <div class="footer-rule"></div>
  <div class="copyright">Copyright &copy; 2019 &nbsp;Vexmore Education. &nbsp;All rights reserved.</div>
</footer>

</body>
</html>
```